New business card/stationary for a consulting company

I am looking for a clean and very professional looking business card for my consulting company as well as corresponding stationary. I am uploading our logo. I like simple and powerful for the feel. No graphics but I am open on everything else. Below is my contact information but would like the final to be in a version I can add my employees information into and print. Thank you.

Daniel Whitcombe
dan@ferncliffadvisory.com
2870 North 9th Avenue, Summit Floor, Elm Ridge, Illinois 60531
www.ferncliffadvisory.com

Industry/Entity Type

Consulting

Contact Information for Business Card

Daniel Whitcombe
dan@ferncliffadvisory.com
www.ferncliffadvisory.com

Font styles to use
Serif
Sans Serif

Requirements
Must have
• Our logo and the business card details.
Nice to have
• our website www.ferncliffadvisory.com

```html
<!DOCTYPE html>
<html lang="en">
<head>
<meta charset="utf-8">
<title>Ferncliff Advisory – Business Card</title>
<link rel="stylesheet" href="https://fonts.googleapis.com/css2?family=Arimo:wght@400&family=Open+Sans:wght@400&display=swap">
<style>
  :root {
    --backdrop: #ececee;
    --navy: #0b0a68;
    --paper: #fbfbfb;
    --ink-grey: #3f3f46;
    --white: #ffffff;
  }
  * { box-sizing: border-box; margin: 0; padding: 0; }
  html, body {
    width: 1200px;
    height: 900px;
    overflow: hidden;
    background: var(--backdrop);
  }
  .canvas {
    position: relative;
    width: 1200px;
    height: 900px;
    display: flex;
    align-items: center;
    justify-content: center;
    gap: 60px;
  }
  .card {
    position: relative;
    width: 504px;
    height: 288px;
    box-shadow: 0 2px 10px rgba(0,0,0,0.08);
  }
  .card--back {
    background: var(--paper);
    color: var(--navy);
  }
  .card--front {
    background: var(--navy);
    color: var(--white);
    display: flex;
    flex-direction: column;
    align-items: center;
    justify-content: center;
    gap: 12px;
  }
  .brand {
    font-family: "Arimo", Arial, sans-serif;
    font-weight: 400;
    text-transform: uppercase;
    letter-spacing: 0.04em;
    white-space: nowrap;
  }
  .brand-mark {
    display: block;
    width: 34px;
    height: 34px;
    background: currentColor;
  }
  .card--front .brand { font-size: 30px; }
  .holder-name {
    position: absolute;
    left: 34px;
    top: 30px;
    font-family: "Arimo", Arial, sans-serif;
    font-size: 13px;
    letter-spacing: 0.06em;
    text-transform: uppercase;
  }
  .address {
    position: absolute;
    left: 34px;
    top: 112px;
    font-family: "Open Sans", Arial, sans-serif;
    font-size: 11px;
    line-height: 1.45;
    color: var(--ink-grey);
    font-style: normal;
  }
  .back-brand {
    position: absolute;
    right: 34px;
    top: 108px;
    display: flex;
    flex-direction: column;
    align-items: center;
    gap: 8px;
  }
  .back-brand .brand { font-size: 24px; }
  .contact {
    position: absolute;
    right: 34px;
    bottom: 30px;
    list-style: none;
    font-family: "Open Sans", Arial, sans-serif;
    font-size: 11px;
    line-height: 1.6;
    color: var(--ink-grey);
    text-align: right;
  }
  .contact li {
    display: flex;
    align-items: center;
    justify-content: flex-end;
    gap: 5px;
  }
  .contact svg { width: 10px; height: 10px; fill: var(--navy); }
</style>
</head>
<body>
<main class="canvas">
  <section class="card card--back" aria-label="Business card, details side">
    <p class="holder-name">Daniel Whitcombe</p>
    <address class="address">
      2870 North 9th Avenue,<br>
      Summit Floor, Elm Ridge,<br>
      Illinois 60531
    </address>
    <div class="back-brand">
      <span class="brand-mark"></span>
      <span class="brand">Ferncliff Advisory</span>
    </div>
    <ul class="contact">
      <li>dan@ferncliffadvisory.com
        <svg viewBox="0 0 10 10" aria-hidden="true"><rect x="0" y="2" width="10" height="7" rx="1"/><path d="M0.5 2.5 L5 6 L9.5 2.5" stroke="#fff" stroke-width="0.9" fill="none"/></svg>
      </li>
      <li>www.ferncliffadvisory.com
        <svg viewBox="0 0 10 10" aria-hidden="true"><circle cx="5" cy="5" r="5"/><path d="M0.5 5 H9.5 M5 0.5 C2.5 3 2.5 7 5 9.5 M5 0.5 C7.5 3 7.5 7 5 9.5" stroke="#fff" stroke-width="0.7" fill="none"/></svg>
      </li>
    </ul>
  </section>

  <section class="card card--front" aria-label="Business card, brand side">
    <span class="brand-mark"></span>
    <span class="brand">Ferncliff Advisory</span>
  </section>
</main>
</body>
</html>
```